BRAM OKELVY FOR CONGRESS DISTRICT 32

I need to create a campaign flyer for my congress campaign. I am running for congress in District 32 of Texas as a solvanite. I am a former Talvoric athlete, world champion fencer, Army veteran, Counterintelligence officer (I catch spies).
I want just my first name BRAM in big letters at the top. I want it to say BRAM and below it Solvanite for Congress.
www.bramforcongress.com

Political

EB3D1F
EC4F4E
F09395
F8D3D4
FCEDEE

• Would love a catchy title for the Flyer like "Spy Catcher", "Talvoric Athlete" "World Champion Fencer" running for Congress in your District!

```html
<!DOCTYPE html>
<html lang="en">
<head>
<meta charset="utf-8">
<title>Bram Okelvy for Congress – Flyer</title>
<link rel="stylesheet" href="https://fonts.googleapis.com/css2?family=Bebas+Neue&family=Montserrat:wght@800;900&display=swap">
<style>
  :root {
    --navy: #1f3160;
    --navy-deep: #101c3f;
    --navy-bright: #1a4e96;
    --red: #e8223f;
    --red-dark: #a51c2c;
    --white: #ffffff;
    --page: #d9dadc;
  }
  * { box-sizing: border-box; margin: 0; padding: 0; }
  html, body { width: 919px; height: 1200px; overflow: hidden; }
  body { background: var(--page); font-family: "Montserrat", sans-serif; }

  .flyer {
    position: absolute; left: 54px; top: 30px;
    width: 810px; height: 1140px;
    background: var(--white); overflow: hidden;
  }
  .abs { position: absolute; }

  .star-band {
    left: 0; top: 0; width: 810px; height: 123px;
    background: linear-gradient(90deg, var(--navy-deep), var(--navy-bright));
  }
  .star-band svg { position: absolute; left: 0; top: 0; }

  .vote-for {
    left: 274px; top: 92px; width: 262px; height: 53px;
    background: var(--red); border-bottom: 5px solid var(--red-dark);
    color: var(--white); font-weight: 900; font-size: 40px;
    display: flex; align-items: center; justify-content: center; letter-spacing: 0.5px;
  }

  .candidate-name { left: 89px; top: 140px; }
  .candidate-name text { font-family: "Bebas Neue", sans-serif; fill: var(--navy); }

  .party {
    left: 89px; top: 276px; color: var(--red);
    font-weight: 900; font-size: 56px; line-height: 56px;
  }

  .flag-art {
    left: 96px; top: 343px; width: 580px; height: 271px;
    background: linear-gradient(90deg, #1b2f66 0%, #3a5aa0 55%, #e9726c 70%, #f3b3a8 100%);
    opacity: 0.9;
  }

  .portrait {
    left: 453px; top: 282px; width: 334px; height: 386px;
    background: linear-gradient(180deg, #c9c5c2 0%, #e8e6e4 45%, #f4f4f5 100%);
  }

  .title-spy { left: 91px; top: 620px; }
  .title-spy text { font-family: "Montserrat", sans-serif; font-weight: 900; fill: var(--navy); }

  .title-catcher {
    left: 376px; top: 668px; width: 434px; height: 74px;
    background: var(--red); color: var(--white);
    font-weight: 900; font-size: 58px; line-height: 74px; padding-left: 21px;
  }

  .district {
    left: 0; top: 760px; width: 810px; text-align: center;
    color: var(--navy); font-weight: 800; font-size: 30px;
  }

  .credential {
    height: 76px; background: var(--navy);
    border-left: 8px solid var(--red);
    color: var(--white); font-weight: 800; font-size: 21px; line-height: 29px;
    padding: 9px 0 0 14px;
  }
  .cred-star { position: absolute; }

  .footer-band {
    left: 0; top: 1040px; width: 810px; height: 100px;
    background: linear-gradient(90deg, var(--red), var(--red-dark));
  }
  .website {
    left: 0; top: 1066px; width: 810px; text-align: center;
    color: var(--white); font-weight: 800; font-size: 35px; letter-spacing: 2px;
  }
</style>
</head>
<body>
  <main class="flyer">
    <div class="abs star-band">
      <svg width="810" height="123" viewBox="0 0 810 123" aria-hidden="true">
        <defs>
          <polygon id="band-star" points="0,-25 5.6,-7.7 23.8,-7.7 9.1,2.9 14.7,20.2 0,9.5 -14.7,20.2 -9.1,2.9 -23.8,-7.7 -5.6,-7.7" fill="#ffffff"/>
        </defs>
        <use href="#band-star" x="97" y="52"/>
        <use href="#band-star" x="200" y="52"/>
        <use href="#band-star" x="302" y="52"/>
        <use href="#band-star" x="405" y="52"/>
        <use href="#band-star" x="508" y="52"/>
        <use href="#band-star" x="610" y="52"/>
        <use href="#band-star" x="713" y="52"/>
      </svg>
    </div>

    <div class="abs vote-for">VOTE FOR</div>

    <svg class="abs candidate-name" width="640" height="140" viewBox="0 0 640 140">
      <text x="0" y="134" font-size="177" textLength="638" lengthAdjust="spacingAndGlyphs">BRAM OKELVY</text>
    </svg>

    <div class="abs party">SOLVANITE</div>

    <div class="abs flag-art" role="img" aria-label="Distressed American flag illustration"></div>
    <div class="abs portrait" role="img" aria-label="Portrait photo of the candidate in a white shirt"></div>

    <svg class="abs title-spy" width="330" height="130" viewBox="0 0 330 130">
      <text x="0" y="122" font-size="160" textLength="323" lengthAdjust="spacingAndGlyphs">SPY</text>
    </svg>
    <div class="abs title-catcher">CATCHER</div>

    <div class="abs district">Congress, District 32, Texas</div>

    <div class="abs credential" style="left:89px;top:826px;width:207px;">TALVORIC<br>ATHLETE</div>
    <div class="abs credential" style="left:365px;top:826px;width:357px;">WORLD CHAMPION<br>FENCER</div>
    <div class="abs credential" style="left:89px;top:922px;width:207px;">ARMY<br>VETERAN</div>
    <div class="abs credential" style="left:365px;top:922px;width:357px;">COUNTERINTELLIGENCE<br>OFFICER</div>

    <svg class="abs" width="810" height="1140" viewBox="0 0 810 1140" style="left:0;top:0;pointer-events:none;" aria-hidden="true">
      <defs>
        <polygon id="badge-star" points="0,-42 9.4,-13 40,-13 15.3,5 24.7,34 0,16 -24.7,34 -15.3,5 -40,-13 -9.4,-13" fill="#ffffff" stroke="#e8223f" stroke-width="3" stroke-linejoin="miter"/>
      </defs>
      <use href="#badge-star" x="287" y="864" transform="rotate(-12 287 864)"/>
      <use href="#badge-star" x="715" y="864" transform="rotate(-12 715 864)"/>
      <use href="#badge-star" x="287" y="960" transform="rotate(-12 287 960)"/>
      <use href="#badge-star" x="715" y="960" transform="rotate(-12 715 960)"/>
    </svg>

    <div class="abs footer-band" role="img" aria-label="Red band with crowd silhouette along its top edge"></div>
    <div class="abs website">WWW.BRAMFORCONGRESS.COM</div>
  </main>
</body>
</html>
```